Flight school sign for building, banner, and bilboard

This sign is primarily for use on the side of our flight school building to draw attention for current and future flight school students. We offer airplane and helicopter flight training, ground school training and seminars, airplane and helicopter rentals, multi-engine training, and more. I would like a professional but exciting sign that can be used across a multitude of signage options such as banners, banner ads, billboard, and other mediums so that our sign is consistent and recognizable.

Contact Information for Business Card

The business card should match our company sign somewhat but not exactly. We want good and exciting imagery or wording and energizing/exciting colors.

```html
<!DOCTYPE html>
<html lang="en">
<head>
<meta charset="utf-8">
<title>Zenith Aviation – Building Sign</title>
<link rel="stylesheet" href="https://fonts.googleapis.com/css2?family=Oswald:wght@500;600;700&family=Rajdhani:wght@700&display=swap">
<style>
  :root {
    --navy: #262a5e;
    --navy-deep: #1d2150;
    --red: #e8243a;
    --white: #ffffff;
    --page: #e9e9ec;
    --photo-sky: #b9c6cf;
    --photo-ground: #8d9a7a;
  }
  * { margin: 0; padding: 0; box-sizing: border-box; }
  html, body {
    width: 1000px;
    height: 1200px;
    overflow: hidden;
    background: var(--page);
  }
  .canvas {
    position: relative;
    width: 1000px;
    height: 1200px;
  }
  .sign {
    position: absolute;
    left: 30px;
    top: 435px;
    width: 940px;
    height: 330px;
    box-shadow: 0 14px 30px rgba(0, 0, 0, 0.28);
  }
  .sign svg { display: block; width: 100%; height: 100%; }
  .brand-name {
    font-family: "Oswald", sans-serif;
    font-weight: 500;
    font-size: 42px;
    letter-spacing: 4px;
    fill: var(--white);
  }
  .service {
    font-family: "Oswald", sans-serif;
    font-weight: 600;
    font-size: 29px;
    letter-spacing: 0.5px;
    fill: var(--white);
  }
  .chevron { fill: var(--red); }
  .headline {
    font-family: "Oswald", sans-serif;
    font-weight: 700;
    text-anchor: middle;
    paint-order: stroke;
    stroke: var(--white);
    stroke-linejoin: round;
  }
  .headline-top { font-size: 72px; fill: var(--navy); stroke-width: 5px; }
  .headline-main { font-size: 104px; fill: var(--red); stroke-width: 7px; }
  .web-address {
    font-family: "Rajdhani", sans-serif;
    font-weight: 700;
    font-size: 48px;
    fill: var(--red);
  }
  .phone-number {
    font-family: "Rajdhani", sans-serif;
    font-weight: 700;
    font-size: 48px;
    fill: var(--white);
  }
</style>
</head>
<body>
<main class="canvas">
  <section class="sign" aria-label="Zenith Aviation flight school sign">
    <svg viewBox="0 0 1575 552" xmlns="http://www.w3.org/2000/svg">
      <defs>
        <linearGradient id="photo-fill" x1="0" y1="0" x2="0" y2="1">
          <stop offset="0" stop-color="var(--photo-sky)"/>
          <stop offset="0.45" stop-color="#7f8f84"/>
          <stop offset="0.7" stop-color="#c9cccf"/>
          <stop offset="1" stop-color="#d9dadb"/>
        </linearGradient>
      </defs>

      <rect class="sign-base" width="1575" height="552" fill="var(--navy)"/>

      <path class="red-sweep"
            d="M690 165 C880 370 1080 492 1300 500 C1470 505 1560 420 1540 290 C1525 190 1470 110 1395 50
               C1500 110 1575 200 1575 270 L1575 552 L1210 552 C1000 470 840 330 690 165 Z"
            fill="var(--red)"/>

      <path class="photo-area" role="img"
            aria-label="Photo of a small white single-engine training aircraft parked on an apron with hills behind"
            d="M505 0 L1575 0 L1575 230 C1560 400 1460 492 1300 492 C1100 488 900 370 705 180 C640 115 560 50 505 0 Z"
            fill="url(#photo-fill)" stroke="var(--navy-deep)" stroke-width="4"/>

      <rect class="plane-graphic" role="img"
            aria-label="Large red airplane graphic flying up to the left"
            x="515" y="8" width="180" height="160" fill="var(--red)"/>

      <text class="headline headline-top" x="1007" y="100" textLength="490" lengthAdjust="spacingAndGlyphs">EXCELLENCE IN</text>
      <text class="headline headline-main" x="1007" y="195" textLength="492" lengthAdjust="spacingAndGlyphs">AVIATION</text>

      <g class="brand">
        <circle cx="278" cy="110" r="40" fill="none" stroke="var(--white)" stroke-width="8"/>
        <text class="brand-name" x="278" y="215" text-anchor="middle" textLength="420" lengthAdjust="spacingAndGlyphs">ZENITH AVIATION</text>
      </g>

      <g class="services">
        <g class="service-item">
          <path class="chevron" d="M62 272 l8 0 l11 11 l-11 11 l-8 0 l11 -11 z M74 272 l8 0 l11 11 l-11 11 l-8 0 l11 -11 z"/>
          <text class="service" x="95" y="294">AIRPLANE AND</text>
          <text class="service" x="95" y="334">HELICOPTER FLIGHT TRAINING</text>
        </g>
        <g class="service-item">
          <path class="chevron" d="M62 367 l8 0 l11 11 l-11 11 l-8 0 l11 -11 z M74 367 l8 0 l11 11 l-11 11 l-8 0 l11 -11 z"/>
          <text class="service" x="95" y="389">AIRPLANE AND</text>
          <text class="service" x="95" y="429">HELICOPTER RENTALS</text>
        </g>
        <g class="service-item">
          <path class="chevron" d="M452 272 l8 0 l11 11 l-11 11 l-8 0 l11 -11 z M464 272 l8 0 l11 11 l-11 11 l-8 0 l11 -11 z"/>
          <text class="service" x="485" y="294">GROUND SCHOOL</text>
          <text class="service" x="485" y="334">TRAINING AND SEMINARS</text>
        </g>
        <g class="service-item">
          <path class="chevron" d="M452 370 l8 0 l11 11 l-11 11 l-8 0 l11 -11 z M464 370 l8 0 l11 11 l-11 11 l-8 0 l11 -11 z"/>
          <text class="service" x="485" y="392">MULTI-ENGINE TRAINING,</text>
          <text class="service" x="485" y="432">AND MORE.</text>
        </g>
      </g>

      <g class="contact-bar">
        <polygon points="0,462 598,462 546,552 0,552" fill="var(--white)"/>
        <polygon points="598,462 1020,462 1210,552 546,552" fill="var(--red)"/>
        <g class="globe-icon" fill="none" stroke="var(--navy)" stroke-width="3">
          <circle cx="79" cy="504" r="15"/>
          <ellipse cx="79" cy="504" rx="6" ry="15"/>
          <line x1="64" y1="504" x2="94" y2="504"/>
          <line x1="67" y1="496" x2="91" y2="496"/>
          <line x1="67" y1="512" x2="91" y2="512"/>
        </g>
        <text class="web-address" x="112" y="520" textLength="412" lengthAdjust="spacingAndGlyphs">ZenithAviation.com</text>
        <g class="phone-icon">
          <circle cx="638" cy="506" r="19" fill="none" stroke="var(--white)" stroke-width="3"/>
          <path d="M631 496 c2 -2 4 -2 5 0 l2 4 c1 2 0 3 -1 4 c1 3 3 5 6 6 c1 -1 2 -2 4 -1 l4 2 c2 1 2 3 0 5 c-3 3 -8 2 -13 -3 c-5 -5 -7 -12 -7 -17 z" fill="var(--white)"/>
        </g>
        <text class="phone-number" x="677" y="522" textLength="313" lengthAdjust="spacingAndGlyphs">(555) 318 2070</text>
      </g>
    </svg>
  </section>
</main>
</body>
</html>
```